Unique Business Card Design

Unique Business Card design for our orthotic and prosthetic company. Our logo is on our website, color is light blue. Unique shape (artificial leg shaped, vertical, etc..) preferred. Logo, business name, individual name and basic demographics needed.

Industry/Entity Type

Business

Contact Information for Business Card

Logo, Industry, Phone # Logo, "Prosthetic & Orthotic Services" Place to add individual name and contact info

Colors
cee9f5

Requirements
Must have
• The icon must be there, placement of "Prosthetic & Orthotic Services" can be moved
Nice to have
• Like the mix of light blue, and a little darker blue. One design included the icons from my website which was a nice touch

```html
<!DOCTYPE html>
<html lang="en">
<head>
<meta charset="utf-8">
<title>Stridewell Inc. — Business Card</title>
<link href="https://fonts.googleapis.com/css2?family=Montserrat:wght@400;600;700&display=swap" rel="stylesheet">
<style>
  :root {
    --bg-dark: #1c1c1c;
    --bg-mid: #6a6a6a;
    --brand-blue: #1f6cc0;
    --brand-blue-deep: #175aa6;
    --brand-blue-light: #3a86d6;
    --card-white: #ffffff;
    --ink-white: #ffffff;
  }
  * { margin: 0; padding: 0; box-sizing: border-box; }
  html, body { width: 1200px; height: 950px; overflow: hidden; }
  body {
    background: radial-gradient(ellipse at 50% 45%, var(--bg-mid) 0%, #3a3a3a 45%, var(--bg-dark) 100%);
    font-family: "Montserrat", Arial, sans-serif;
    position: relative;
  }
  .card {
    position: absolute;
    width: 600px;
    height: 340px;
    border-radius: 22px;
    overflow: hidden;
    box-shadow: 0 18px 40px rgba(0,0,0,0.5);
  }
  /* Front */
  .card-front {
    left: 90px; top: 90px;
    background: linear-gradient(135deg, var(--brand-blue-light) 0%, var(--brand-blue) 50%, var(--brand-blue-deep) 100%);
  }
  .front-brand {
    position: absolute; left: 88px; top: 110px;
    display: flex; align-items: center; gap: 26px;
  }
  .brand-dot {
    width: 96px; height: 96px; border-radius: 50%;
    background: var(--card-white); flex: none;
  }
  .brand-name {
    color: var(--ink-white); font-weight: 700; font-size: 30px; letter-spacing: 0.5px;
    border-bottom: 3px solid var(--ink-white); padding-bottom: 4px;
  }
  .brand-tagline { color: var(--ink-white); font-size: 15px; font-weight: 400; margin-top: 6px; font-style: normal; }
  .front-web {
    position: absolute; left: 0; right: 0; bottom: 46px;
    display: flex; align-items: center; justify-content: center; gap: 14px;
    color: var(--ink-white); font-size: 13px;
  }
  .front-web .rule { width: 120px; height: 1px; background: rgba(255,255,255,0.7); }

  /* Back */
  .card-back {
    left: 510px; top: 510px;
    background: linear-gradient(135deg, var(--brand-blue-light) 0%, var(--brand-blue) 55%, var(--brand-blue-deep) 100%);
  }
  .back-arc {
    position: absolute; left: 300px; top: -170px;
    width: 470px; height: 470px; border-radius: 50%;
    background: var(--card-white);
  }
  .back-brand {
    position: absolute; left: 330px; top: 100px;
    display: flex; align-items: center; gap: 14px;
  }
  .back-brand .brand-dot { width: 58px; height: 58px; background: var(--brand-blue); }
  .back-brand .brand-name { color: var(--brand-blue); font-size: 20px; border-bottom-color: var(--brand-blue); border-bottom-width: 2px; }
  .back-brand .brand-tagline { color: var(--brand-blue); font-size: 11px; }
  .contact {
    position: absolute; left: 40px; top: 120px; color: var(--ink-white);
  }
  .person-name { font-weight: 700; font-size: 20px; }
  .person-title { font-weight: 600; font-size: 13px; margin-top: 2px; }
  .address { font-size: 13px; margin-top: 14px; line-height: 1.4; }
  .contact-list { list-style: none; margin-top: 8px; font-size: 13px; }
  .contact-list li { display: flex; align-items: center; gap: 9px; height: 21px; }
  .contact-list svg { width: 14px; height: 14px; flex: none; }
</style>
</head>
<body>

<section class="card card-front" aria-label="Card front">
  <div class="front-brand">
    <div class="brand-dot"></div>
    <div>
      <div class="brand-name">STRIDEWELL INC.</div>
      <div class="brand-tagline">Prosthetic &amp; Orthotic Services</div>
    </div>
  </div>
  <div class="front-web"><span class="rule"></span><span>www.stridewellinc.com</span><span class="rule"></span></div>
</section>

<section class="card card-back" aria-label="Card back">
  <div class="back-arc"></div>
  <div class="back-brand">
    <div class="brand-dot"></div>
    <div>
      <div class="brand-name">STRIDEWELL INC.</div>
      <div class="brand-tagline">Prosthetic &amp; Orthotic Services</div>
    </div>
  </div>
  <div class="contact">
    <div class="person-name">Miriam Castell</div>
    <div class="person-title">CO LPO</div>
    <div class="address">820 Linden Ave.<br>Brookfield, NY 11590</div>
    <ul class="contact-list">
      <li><svg viewBox="0 0 14 14" aria-hidden="true"><path d="M3 1h3l1 3-2 1a8 8 0 0 0 4 4l1-2 3 1v3a1 1 0 0 1-1 1A12 12 0 0 1 2 2a1 1 0 0 1 1-1z" fill="#fff"/></svg>555.210.4400</li>
      <li><svg viewBox="0 0 14 14" aria-hidden="true"><rect x="3.5" y="1" width="7" height="12" rx="1.2" fill="none" stroke="#fff" stroke-width="1.5"/><circle cx="7" cy="11" r="0.8" fill="#fff"/></svg>555.210.4419</li>
      <li><svg viewBox="0 0 14 14" aria-hidden="true"><rect x="3" y="1" width="8" height="4" fill="#fff"/><rect x="1" y="5" width="12" height="6" rx="1" fill="#fff"/><rect x="3" y="9" width="8" height="4" fill="#fff" stroke="#1f6cc0" stroke-width="0.8"/></svg>555-7301628</li>
      <li><svg viewBox="0 0 14 14" aria-hidden="true"><rect x="1" y="3" width="12" height="8" fill="none" stroke="#fff" stroke-width="1.4"/><path d="M1 3l6 5 6-5" fill="none" stroke="#fff" stroke-width="1.4"/></svg>mcastell@stridewellinc.com</li>
      <li><svg viewBox="0 0 14 14" aria-hidden="true"><circle cx="7" cy="7" r="6" fill="#fff"/><path d="M1 7h12M7 1c-3 3-3 9 0 12M7 1c3 3 3 9 0 12" fill="none" stroke="#1f6cc0" stroke-width="1"/></svg>www.stridewellinc.com</li>
    </ul>
  </div>
</section>

</body>
</html>
```